Online interactive calendar for training organisation

We have a new website being made and need a design for an online calendar that is interactive and very simple and easy to use. On our main page this calendar will include all of our courses (approx 30 different ones with up to 8 different locations). On our sub pages which have course information, the calendar will only include details of that specific course. Details needed are: Course code, course name/title, date, duration (1/2 day - 5 days), location, price, discount price. Maybe also a key for available or limited spots left? We want a section at the top of the calendar to be able to filter by location or course, and maybe to filter by month also? I have included a spreadsheet with a sample of our courses with this information. Also a sample draft of the main page on our new webpage to show the colour green which is our company colour. Main notes - we want as simple, effective and easy to use as possible.
We will need to know what plug in we can use to get the design you have created.

Target Market(s)

Mining and construction - both companies and individuals

Number of Pages Required

1 page

Colors
cadf82

Requirements
Must have
• Be simple, easy to use, effective.

```html
<!DOCTYPE html>
<html lang="en">
<head>
<meta charset="utf-8">
<title>Time Table</title>
<link rel="stylesheet" href="https://fonts.googleapis.com/css2?family=IBM+Plex+Sans:wght@400;500;600;700&display=swap">
<style>
  :root {
    --green: #8cc63f;
    --ink: #111111;
    --text: #222222;
    --muted: #555555;
    --border: #b9b9b9;
    --rule: #c4c4c4;
    --chip: #efefef;
    --dark: #333333;
    --paper: #ffffff;
    --discount: #efefef;
    --required: #e02020;
  }
  * { box-sizing: border-box; margin: 0; padding: 0; }
  html, body { width: 1200px; height: 697px; overflow: hidden; background: var(--paper); }
  body { font-family: "IBM Plex Sans", Arial, sans-serif; color: var(--text); position: relative; }

  .page-title {
    position: absolute; top: 38px; left: 0; width: 1200px;
    text-align: center; font-size: 25px; font-weight: 700; color: var(--ink); letter-spacing: 0.3px;
  }
  .title-rule { position: absolute; left: 577px; top: 80px; width: 47px; height: 4px; background: var(--rule); }

  .filter {
    position: absolute; top: 126px; width: 198px; height: 42px;
    border: 2px solid var(--border); padding: 7px 10px;
  }
  .filter.is-active { border-color: var(--green); }
  .filter-label { display: block; font-size: 9.5px; font-weight: 600; color: var(--ink); line-height: 12px; }
  .filter-label em { color: var(--required); font-style: normal; }
  .filter-value { display: block; font-size: 11px; color: var(--muted); line-height: 14px; letter-spacing: 0.3px; }
  .filter.is-active .filter-value { color: var(--green); font-weight: 500; }
  .filter-chevron { position: absolute; right: 14px; top: 16px; }

  .course-card {
    position: absolute; width: 270px; height: 207px;
    border: 1px solid var(--border); background: var(--paper); overflow: hidden;
  }
  .course-date {
    position: absolute; left: 26px; top: 18px; width: 158px;
    font-size: 12px; color: var(--muted); padding-bottom: 5px; border-bottom: 2px solid #d6d6d6; white-space: nowrap;
  }
  .course-date .sep { margin: 0 7px; }
  .course-name {
    position: absolute; left: 26px; top: 56px; width: 200px;
    font-size: 15.5px; line-height: 19px; color: var(--ink);
  }
  .course-name em { color: var(--required); font-style: normal; font-size: 12px; }
  .course-tag { position: absolute; left: 24px; top: 111px; height: 26px; display: flex; }
  .tag-duration {
    height: 26px; padding: 0 10px; background: var(--chip); border: 1px solid #d0d0d0; border-right: 0;
    font-size: 11.5px; line-height: 24px; color: var(--ink);
  }
  .tag-location {
    height: 26px; padding: 0 16px 0 11px; background: var(--dark); color: #fff;
    font-size: 13px; font-weight: 700; line-height: 26px; letter-spacing: 0.4px;
    clip-path: polygon(0 0, 88% 0, 100% 100%, 0 100%);
  }
  .course-price {
    position: absolute; left: 26px; top: 148px;
    font-size: 23px; font-weight: 700; color: var(--green);
  }
  .discount { position: absolute; right: 0; bottom: 0; width: 89px; height: 56px; }
  .discount svg { position: absolute; inset: 0; }
  .discount-label { position: absolute; left: 16px; top: 17px; font-size: 10px; color: var(--muted); letter-spacing: 0.3px; }
  .discount-amount { position: absolute; left: 15px; top: 30px; font-size: 15.5px; color: var(--ink); }
</style>
</head>
<body>
  <h1 class="page-title">TIME TABLE</h1>
  <div class="title-rule"></div>

  <div class="filter is-active" style="left:287px">
    <span class="filter-label">LOCATION<em>*</em></span>
    <span class="filter-value">YATALA</span>
    <svg class="filter-chevron" width="10" height="7" viewBox="0 0 10 7"><path d="M1 1l4 4 4-4" fill="none" stroke="#333" stroke-width="1.8"/></svg>
  </div>
  <div class="filter" style="left:501px">
    <span class="filter-label">COURSE<em>*</em></span>
    <span class="filter-value">SELECT COURSE</span>
    <svg class="filter-chevron" width="10" height="7" viewBox="0 0 10 7"><path d="M1 1l4 4 4-4" fill="none" stroke="#333" stroke-width="1.8"/></svg>
  </div>
  <div class="filter" style="left:717px">
    <span class="filter-label">MONTH<em>*</em></span>
    <span class="filter-value">SELECT MONTH</span>
    <svg class="filter-chevron" width="10" height="7" viewBox="0 0 10 7"><path d="M1 1l4 4 4-4" fill="none" stroke="#333" stroke-width="1.8"/></svg>
  </div>

  <article class="course-card" style="left:186px; top:212px">
    <p class="course-date">29 October 2019<span class="sep">|</span>8:00 AM</p>
    <h2 class="course-name">RIIHAN304D Work safely at heights <em>*</em></h2>
    <div class="course-tag"><span class="tag-duration">1 DAY</span><span class="tag-location">YATALA</span></div>
    <p class="course-price">$500.00</p>
    <div class="discount">
      <svg width="89" height="56" viewBox="0 0 89 56"><polygon points="0,0 89,9 89,56 4,56" fill="#efefef"/><polyline points="4,56 0,0 89,9" fill="none" stroke="#bbb" stroke-width="1"/></svg>
      <span class="discount-label">DISCOUNT</span><span class="discount-amount">$120.00</span>
    </div>
  </article>

  <article class="course-card" style="left:467px; top:212px">
    <p class="course-date">29 October 2019<span class="sep">|</span>8:00 AM</p>
    <h2 class="course-name">RIIHAN304D Work safely at heights</h2>
    <div class="course-tag"><span class="tag-duration">1 DAY</span><span class="tag-location">YATALA</span></div>
    <p class="course-price">$500.00</p>
    <div class="discount">
      <svg width="89" height="56" viewBox="0 0 89 56"><polygon points="0,0 89,9 89,56 4,56" fill="#efefef"/><polyline points="4,56 0,0 89,9" fill="none" stroke="#bbb" stroke-width="1"/></svg>
      <span class="discount-label">DISCOUNT</span><span class="discount-amount">$120.00</span>
    </div>
  </article>

  <article class="course-card" style="left:747px; top:212px">
    <p class="course-date">30 January 2020<span class="sep">|</span>8:00 AM</p>
    <h2 class="course-name">HLTAID005 Confined space - practical</h2>
    <div class="course-tag"><span class="tag-duration">1/2 DAY</span><span class="tag-location">YATALA</span></div>
    <p class="course-price">$80.00</p>
  </article>

  <article class="course-card" style="left:186px; top:434px">
    <p class="course-date">15 November 2020<span class="sep">|</span>8:00 AM</p>
    <h2 class="course-name">HLTAID001 First Aid - practical only</h2>
    <div class="course-tag"><span class="tag-duration">1/2 DAY</span><span class="tag-location">YATALA</span></div>
    <p class="course-price">$80.00</p>
  </article>

  <article class="course-card" style="left:467px; top:434px">
    <p class="course-date">28 October 2019<span class="sep">|</span>8:00 AM</p>
    <h2 class="course-name">CPCCCM208 Dogging &amp; TLILIC0005</h2>
    <div class="course-tag"><span class="tag-duration">1 DAY</span><span class="tag-location">YATALA</span></div>
    <p class="course-price">$500.00</p>
    <div class="discount">
      <svg width="89" height="56" viewBox="0 0 89 56"><polygon points="0,0 89,9 89,56 4,56" fill="#efefef"/><polyline points="4,56 0,0 89,9" fill="none" stroke="#bbb" stroke-width="1"/></svg>
      <span class="discount-label" style="left:13px">DISCOUNT</span><span class="discount-amount" style="left:12px">$1200.00</span>
    </div>
  </article>
</body>
</html>
```